Process Serving Company needs a letterhead design

Looking to have a letterhead designed for letters to attorneys advertising our business. We would like something eye catching but professional. Colors and logos are attached. Please add "Process Service and Attorney Support" near the logo or header

Target Market(s)

Attorneys

Font styles to use
Serif
Sans Serif

Colors
33a6d7
0255a3
85cae6
cee9f5
ecf7fb

```html
<!DOCTYPE html>
<html lang="en">
<head>
<meta charset="utf-8">
<title>Halvorsen Courier Letterhead</title>
<link rel="stylesheet" href="https://fonts.googleapis.com/css2?family=Lato:wght@400;700&family=Kaushan+Script&family=Arimo&display=swap">
<style>
  :root{
    --brand-blue:#1694d2;
    --ink:#3a3a3a;
    --text:#555555;
    --dark:#1c1c1c;
    --paper:#ffffff;
    --backdrop:#e3e3e8;
  }
  *{margin:0;padding:0;box-sizing:border-box}
  html,body{width:1200px;height:1200px;overflow:hidden;background:var(--backdrop)}
  .letterhead{
    position:absolute;left:246px;top:100px;width:708px;height:1000px;
    background:var(--paper);box-shadow:0 6px 24px rgba(0,0,0,.12);
    font-family:'Lato',sans-serif;color:var(--text);overflow:hidden;
  }
  .brand{
    position:absolute;left:52px;top:48px;display:flex;align-items:center;gap:10px;
  }
  .brand-square{width:26px;height:26px;background:var(--brand-blue)}
  .brand-name{
    font-family:'Lato',sans-serif;font-weight:700;font-size:21px;line-height:1;
    color:var(--brand-blue);white-space:nowrap;
  }
  .contact{
    position:absolute;top:48px;font-family:'Arimo',sans-serif;font-size:10px;color:var(--ink);
  }
  .contact li{list-style:none;display:flex;align-items:center;gap:6px;height:18px;white-space:nowrap}
  .contact svg{width:10px;height:10px;fill:var(--brand-blue)}
  .contact-phones{left:410px}
  .contact-divider{position:absolute;left:514px;top:48px;width:1px;height:28px;background:#9a9a9a}
  .contact-web{left:531px}
  .accent{color:var(--brand-blue)}
  .letter-body{
    position:absolute;left:52px;top:286px;width:553px;font-size:13.4px;line-height:21.4px;
  }
  .salutation{font-weight:700;color:var(--ink);margin-bottom:15px}
  .letter-body p.copy{margin-bottom:16px;text-align:justify}
  .closing{margin-top:28px;font-size:16px;color:var(--ink)}
  .signature{font-family:'Kaushan Script',cursive;font-size:27px;color:var(--brand-blue);margin-top:2px}
  .footer-wave{position:absolute;left:0;bottom:0;width:708px;height:94px}
  .address{
    position:absolute;left:52px;bottom:26px;font-family:'Arimo',sans-serif;font-size:10px;color:#fff;
    display:flex;align-items:center;gap:5px;
  }
  .address svg{width:9px;height:9px;fill:#fff}
</style>
</head>
<body>
<main class="letterhead">
  <header>
    <div class="brand">
      <span class="brand-square"></span>
      <span class="brand-name">Halvorsen Courier</span>
    </div>
    <ul class="contact contact-phones">
      <li><svg viewBox="0 0 10 10"><path d="M2 0.5 3.8 2.6 2.9 3.8C3.5 5 4.9 6.5 6.2 7.1L7.4 6.2 9.5 8 8.4 9.5C4.4 9.3 0.7 5.6 0.5 1.6Z"/></svg>555 210 4400</li>
      <li><svg viewBox="0 0 10 10"><path d="M2.3 2 7.7 2 9 5 9 8.5 7.8 8.5 7.8 7.5 2.2 7.5 2.2 8.5 1 8.5 1 5ZM2.8 3 2.2 4.8 7.8 4.8 7.2 3Z"/></svg>555 210 4411</li>
    </ul>
    <span class="contact-divider"></span>
    <ul class="contact contact-web">
      <li><svg viewBox="0 0 10 10"><path d="M0.5 2 9.5 2 9.5 8 0.5 8ZM1.3 2.8 5 5.4 8.7 2.8Z"/></svg><span>Dana@<span class="accent">HLCourier</span>.com</span></li>
      <li><svg viewBox="0 0 10 10"><path d="M5 0.5A4.5 4.5 0 1 0 5 9.5 4.5 4.5 0 1 0 5 0.5ZM5 1.5C5.8 2.3 6.2 3.4 6.3 4.5H3.7C3.8 3.4 4.2 2.3 5 1.5ZM1.5 4.5H2.8C2.9 3.5 3.2 2.6 3.6 1.8 2.5 2.3 1.7 3.3 1.5 4.5ZM1.5 5.5C1.7 6.7 2.5 7.7 3.6 8.2 3.2 7.4 2.9 6.5 2.8 5.5ZM3.7 5.5C3.8 6.6 4.2 7.7 5 8.5 5.8 7.7 6.2 6.6 6.3 5.5ZM7.2 5.5C7.1 6.5 6.8 7.4 6.4 8.2 7.5 7.7 8.3 6.7 8.5 5.5ZM8.5 4.5C8.3 3.3 7.5 2.3 6.4 1.8 6.8 2.6 7.1 3.5 7.2 4.5Z"/></svg><span class="accent">HLCourier.com</span></li>
    </ul>
  </header>

  <section class="letter-body">
    <p class="salutation">Dear Mr. Lorem,</p>
    <p class="copy">Lorem ipsum dolor sit amet, consectetuer adipiscing elit, sed diam nonummy nibh euismod tincidunt ut laoreet dolore magna aliquam erat volutpat. Ut wisi enim ad minim veniam, quis nostrud exerci tation ullamcorper suscipit lobortis nisl ut aliquip ex ea commodo consequat. Duis autem vel eum iriure dolor in hendiusto odio dignissim qui blandit praesent luptatum zzril delenit augue duis dolore te feugait nulla facilisi.</p>
    <p class="copy">Lorem ipsum dolor sit amet, consectetuer adipiscing elit, sed diam nonummy nibh euismod tincidunt ut laoreet dolore magna aliquam erat volutpat. Ut wisi enim ad minim veniam, quis nostrud exerci tation ullamcorper suscipit lobortis nisl ut aliquip ex ea commodo consequat. Duis autem vel eum iriure dolor in hendiusto odio dignissim qui blandit praesent luptatum zzril delenit augue duis dolore te feugait nulla facilisi.</p>
    <p class="copy">Lorem ipsum dolor sit amet, consectetuer adipiscing elit, sed diam nonummy nibh euismod tincidunt ut laoreet dolore magna aliquam erat volutpat. Ut wisi enim ad minim veniam, quis nostrud exerci tation ullamcorper suscipit lobortis nisl ut aliquip ex ea commodo consequat. Duis autem vel eum iriure dolor in hendiusto odio dignissim qui blandit praesent luptatum zzril delenit augue duis dolore te feugait nulla facilisi.</p>
    <p class="closing">Sincerely Your,</p>
    <p class="signature">Your Name</p>
  </section>

  <footer>
    <svg class="footer-wave" viewBox="0 0 708 94" preserveAspectRatio="none">
      <path d="M0 26 C120 6 250 6 420 40 C540 64 640 60 708 34 L708 94 0 94Z" fill="var(--brand-blue)"/>
      <path d="M0 26 C120 6 250 6 420 40 C540 64 640 60 708 34 L708 29 C640 53 540 56 420 33 C250 0 120 0 0 18Z" fill="var(--dark)"/>
      <path d="M0 26 C120 6 250 6 420 40 C540 64 640 60 708 34" fill="none" stroke="#fff" stroke-width="2.5"/>
    </svg>
    <p class="address"><svg viewBox="0 0 10 10"><path d="M5 0.5C3.1 0.5 1.8 1.9 1.8 3.7 1.8 6 5 9.5 5 9.5S8.2 6 8.2 3.7C8.2 1.9 6.9 0.5 5 0.5ZM5 2.4A1.3 1.3 0 1 1 5 5 1.3 1.3 0 1 1 5 2.4Z"/></svg>4120 E Canyon Rd STE 18, Mesa AZ 85201</p>
  </footer>
</main>
</body>
</html>
```